The K7 Momentum Collective Website

We have a pitch deck and messaging drafted. Target audience is academic institutions and VC investors that have seed money in start ups.

Need a basic website

Industry/Entity Type

LIfe Science, Diagnostic, medical device.

Coding

Coded - Design and coding required

Number of Pages Required

5+ page

```html
<!DOCTYPE html>
<html lang="en">
<head>
<meta charset="utf-8">
<title>The K7 Momentum Collective</title>
<link href="https://fonts.googleapis.com/css2?family=Lato:wght@400;700;900&family=Montserrat:wght@600;700;800&display=swap" rel="stylesheet">
<style>
:root{
  --blue:#0b6fc1;
  --blue-dark:#0857a0;
  --ink:#111418;
  --text:#2c2f33;
  --grey:#9a9da2;
  --soft:#eef0f3;
  --white:#ffffff;
  --black:#000000;
}
*{margin:0;padding:0;box-sizing:border-box}
html,body{width:1200px;height:3585px;overflow:hidden}
body{position:relative;font-family:'Lato',sans-serif;color:var(--text);background:var(--white)}
.abs{position:absolute}
a{color:inherit;text-decoration:none}

/* header */
.site-header{position:absolute;left:0;top:0;width:1200px;height:122px;background:var(--white);z-index:5}
.brand{position:absolute;left:67px;top:54px;font-family:'Montserrat',sans-serif;font-weight:700;font-size:20px;color:var(--blue);letter-spacing:-.2px;white-space:nowrap}
.topbar{position:absolute;left:415px;top:0;width:785px;height:56px;background:var(--blue);border-bottom-left-radius:40px;color:var(--white);font-weight:700;font-size:16px;white-space:nowrap}
.topbar .phone{position:absolute;left:37px;top:17px}
.topbar .mail{position:absolute;left:225px;top:17px}
.topbar .sep{position:absolute;left:205px;top:16px;width:1px;height:22px;background:rgba(255,255,255,.7)}
.social{position:absolute;width:26px;height:26px;border:2px solid var(--white);border-radius:50%;top:15px}
.main-nav{position:absolute;top:80px;font-size:14px;color:var(--ink);white-space:nowrap}
.main-nav.active{color:var(--blue);text-decoration:underline;font-weight:700}
.nav-cta{position:absolute;left:969px;top:67px;width:119px;height:42px;border-radius:21px;background:var(--blue);color:var(--white);font-weight:900;font-size:13px;text-align:center;line-height:42px;box-shadow:0 3px 6px rgba(0,0,0,.25)}

/* hero */
.hero{position:absolute;left:0;top:122px;width:1200px;height:560px;overflow:hidden}
.hero-photo{position:absolute;inset:0;background:linear-gradient(180deg,#e9eef1 0%,#d7dde2 45%,#9aa3a8 70%,#3b4248 100%)}
.hero-welcome{position:absolute;left:0;width:1200px;top:72px;text-align:center;font-family:'Montserrat',sans-serif;font-weight:800;font-size:38px;color:var(--ink)}
.hero-title{position:absolute;left:0;width:1200px;top:124px;text-align:center;font-family:'Montserrat',sans-serif;font-weight:700;font-size:50px;color:var(--blue);letter-spacing:-.5px}
.hero-btn{position:absolute;left:527px;top:226px;width:146px;height:46px;border-radius:23px;background:var(--blue);color:var(--white);font-weight:900;font-size:15px;text-align:center;line-height:46px;box-shadow:0 3px 6px rgba(0,0,0,.3)}
.dot{position:absolute;left:1134px;width:10px;height:10px;border-radius:50%;background:#9cc4e6}
.dot.on{background:var(--blue)}

/* about */
.about-photo{position:absolute;left:121px;top:736px;width:398px;height:398px;border-radius:50%;background:radial-gradient(circle at 55% 40%,#6f8fb4,#1f4f86 60%,#0d2e57)}
.about-title{position:absolute;left:597px;top:738px;font-size:31px;font-weight:400;color:var(--ink);white-space:nowrap}
.about-title strong{color:var(--blue);font-weight:900}
.about-copy{position:absolute;left:597px;top:785px;width:490px;font-size:14.5px;line-height:25.5px}
.tick-list{list-style:none;margin-top:6px}
.tick-list li{position:relative;padding-left:24px;margin-bottom:5px}
.tick-list li svg{position:absolute;left:0;top:8px}
.btn{display:inline-block;background:var(--blue);color:var(--white);font-weight:900;border-radius:22px;text-align:center}
.about-btn{position:absolute;left:597px;top:1100px;width:145px;height:46px;line-height:46px;font-size:15px;box-shadow:0 3px 6px rgba(0,0,0,.25)}

/* discovery */
.discovery{position:absolute;left:0;top:1208px;width:1200px;height:444px;background:var(--soft)}
.section-title{position:absolute;left:0;width:1200px;text-align:center;font-size:35px;color:var(--ink);font-weight:400}
.section-title strong{color:var(--blue);font-weight:700}
.card{position:absolute;top:120px;width:252px;height:262px;background:var(--white);box-shadow:0 2px 8px rgba(0,0,0,.08);text-align:center;overflow:hidden}
.card::before{content:"";position:absolute;left:0;top:0;border-top:34px solid var(--blue);border-right:34px solid transparent}
.card .icon{position:absolute;left:86px;top:24px;width:80px;height:80px;border-radius:14px;background:#e2ecf6}
.card h3{position:absolute;left:0;width:100%;top:132px;font-size:18px;font-weight:900;color:var(--ink)}
.card p{position:absolute;left:10px;right:10px;top:160px;font-size:14.5px;line-height:26px}
.card.featured{background:linear-gradient(180deg,#1b5f9f,#0c4784)}
.card.featured::before{display:none}
.card.featured .icon{background:rgba(255,255,255,.2)}
.card.featured h3,.card.featured p{color:var(--white)}

/* problem */
.problem{position:absolute;left:0;top:1652px;width:1200px;height:447px;background:var(--blue)}
.problem-photo{position:absolute;left:600px;top:0;width:600px;height:447px;background:linear-gradient(90deg,var(--blue) 0%,#3b6f9c 30%,#7d98ad 60%,#a9b7c0 100%)}
.problem-title{position:absolute;left:111px;top:44px;font-size:36px;color:var(--white);font-weight:400}
.problem-title strong{font-weight:900}
.problem-copy{position:absolute;left:111px;top:98px;width:500px;color:var(--white);font-size:14.5px;line-height:25.5px}
.problem-copy ul{list-style:none;margin:6px 0}
.problem-copy li{position:relative;padding-left:20px;margin-bottom:9px}
.problem-copy li svg{position:absolute;left:0;top:8px}
.problem-btn{position:absolute;left:111px;top:339px;width:124px;height:42px;line-height:42px;background:var(--white);color:var(--blue);font-weight:700;font-size:16px;border-radius:4px;text-align:center}

/* team */
.member{position:absolute;width:273px;text-align:center}
.member .photo{width:273px;height:260px;background:linear-gradient(180deg,#e4e5e7,#c9ccd0)}
.member .plate{position:relative;margin:-40px auto 0;width:237px;height:46px;background:var(--white);border-radius:6px 6px 0 0}
.member h4{font-size:19px;font-weight:900;color:var(--ink);line-height:46px}
.member.mid h4{color:var(--blue)}
.member p{font-size:14.5px;line-height:26px;margin:-4px 10px 0}
.member .email{margin-top:10px;font-size:14.5px;font-weight:700;color:var(--blue)}
.member .email svg{vertical-align:-2px;margin-right:10px}

/* contact */
.contact-head{position:absolute;left:114px;top:2778px;font-size:20px;font-weight:900;color:var(--ink)}
.info-row{position:absolute;left:111px;display:flex;align-items:center;font-size:15px;color:var(--ink);font-weight:700;line-height:25px;white-space:nowrap}
.info-icon{width:46px;height:46px;border-radius:50%;background:var(--blue);display:flex;align-items:center;justify-content:center;margin-right:14px;flex:none}
.field{position:absolute;background:var(--white);box-shadow:0 1px 6px rgba(0,0,0,.12);font-size:14px;color:#666;padding:16px 16px}
.submit{position:absolute;left:508px;top:3041px;width:144px;height:45px;line-height:45px;font-size:15px}

/* footer */
.footer{position:absolute;left:0;top:3110px;width:1200px;height:475px}
.footer-brand{position:absolute;left:0;width:1200px;top:196px;text-align:center;font-family:'Montserrat',sans-serif;font-weight:700;font-size:24px;color:var(--white)}
.footer-nav{position:absolute;top:300px;font-size:15px;color:var(--white);transform:translateX(-50%);white-space:nowrap}
.fsocial{position:absolute;top:350px;width:33px;height:33px;border-radius:50%;background:var(--white)}
.copyright{position:absolute;left:0;width:1200px;top:408px;text-align:center;color:var(--white);font-size:15px}
</style>
</head>
<body>

<header class="site-header">
  <div class="brand">THE K7 MOMENTUM COLLECTIVE</div>
  <div class="topbar">
    <span class="phone"><svg width="13" height="13" viewBox="0 0 24 24"><path fill="#fff" d="M6.6 10.8a15 15 0 0 0 6.6 6.6l2.2-2.2a1 1 0 0 1 1-.25 11 11 0 0 0 3.6.6 1 1 0 0 1 1 1V20a1 1 0 0 1-1 1A17 17 0 0 1 3 4a1 1 0 0 1 1-1h3.5a1 1 0 0 1 1 1c0 1.25.2 2.45.6 3.6a1 1 0 0 1-.25 1z"/></svg>&nbsp; +1 555 010 4477</span>
    <span class="sep"></span>
    <span class="mail"><svg width="13" height="11" viewBox="0 0 24 18"><path fill="#fff" d="M0 0h24v3L12 10 0 3zM0 6l12 7 12-7v12H0z"/></svg>&nbsp; info@k7momentumcollective.com</span>
    <span class="social" style="left:535px"></span>
    <span class="social" style="left:571px"></span>
    <span class="social" style="left:607px"></span>
    <span class="social" style="left:643px"></span>
  </div>
  <a class="main-nav active" style="left:422px">HOME</a>
  <a class="main-nav" style="left:501px">ABOUT</a>
  <a class="main-nav" style="left:586px">OUR TEAM</a>
  <a class="main-nav" style="left:693px">PLAN ELEMENTS</a>
  <a class="main-nav" style="left:837px">THE SOLUTIONS</a>
  <a class="nav-cta">CONTACT US</a>
</header>

<section class="hero">
  <div class="hero-photo" role="img" aria-label="Three colleagues meeting around a laptop in a bright office with plants"></div>
  <h1 class="hero-welcome">WELCOME TO</h1>
  <div class="hero-title">THE K7 MOMENTUM COLLECTIVE</div>
  <a class="hero-btn">GET STARTED</a>
  <span class="dot on" style="top:144px"></span>
  <span class="dot" style="top:161px"></span>
  <span class="dot" style="top:178px"></span>
  <svg class="abs" style="left:0;top:440px" width="1200" height="120" viewBox="0 0 1200 120">
    <path d="M0 40 Q 600 150 1200 40 L1200 120 L0 120 Z" fill="var(--white)"/>
  </svg>
</section>

<section class="about">
  <div class="about-photo" role="img" aria-label="Businessman working at a laptop with glowing data charts"></div>
  <h2 class="about-title">ABOUT <strong>K7 MOMENTUM COLLECTIVE</strong></h2>
  <div class="about-copy">
    <p>The K7 Momentum Collective (K7) rapidly brings innovative &amp; transformational IP to market by assisting with all elements of a company’s development.</p>
    <ul class="tick-list">
      <li><svg width="12" height="11" viewBox="0 0 12 11"><path d="M0 4h7V0l5 5.5L7 11V7H0z" fill="#555"/></svg>We Are...experienced in strategic business planning and execution, and operational excellence.</li>
      <li><svg width="12" height="11" viewBox="0 0 12 11"><path d="M0 4h7V0l5 5.5L7 11V7H0z" fill="#555"/></svg>We Have...100 years of collective experiences and vast network of people, partners, and processes.</li>
      <li><svg width="12" height="11" viewBox="0 0 12 11"><path d="M0 4h7V0l5 5.5L7 11V7H0z" fill="#555"/></svg>We Can...serve as the initial executive team to ensure strategic alignment with a focus on marketplace.</li>
      <li><svg width="12" height="11" viewBox="0 0 12 11"><path d="M0 4h7V0l5 5.5L7 11V7H0z" fill="#555"/></svg>We Will...remove the uncertainty and confusion common in the initial stages of a company’s formation.</li>
    </ul>
  </div>
  <a class="btn about-btn">READ MORE</a>
</section>

<section class="discovery">
  <h2 class="section-title" style="top:56px">Discovery <strong>to Market</strong></h2>
  <div class="card" style="left:63px">
    <div class="icon" role="img" aria-label="Magnifying glass over a lightbulb icon"></div>
    <h3>Discovery</h3>
    <p>Business model, Org structure &amp;<br>planning, Cash planning,Fund<br>raising</p>
  </div>
  <div class="card" style="left:337px">
    <div class="icon" role="img" aria-label="Head with gears icon"></div>
    <h3>Innovative IP</h3>
    <p>Inventor Disclosure,Provisional<br>Patent,Licensing<br>agreement</p>
  </div>
  <div class="card featured" style="left:612px" role="img" aria-label="Strategy card over an office photo">
    <div class="icon" role="img" aria-label="Chart board with magnifier icon"></div>
    <h3>Strategic Business Plan</h3>
    <p>Invention Assessment,Voice of<br>Customer,Product Definition<br>Business Model/Plan,Pitch Deck</p>
  </div>
  <div class="card" style="left:887px">
    <div class="icon" role="img" aria-label="Presenter and team icon"></div>
    <h3>Company Formation</h3>
    <p>Experienced management<br>How to build out the initial team<br>Product definition</p>
  </div>
</section>

<section class="problem">
  <div class="problem-photo" role="img" aria-label="Man in glasses working on a laptop by a window"></div>
  <h2 class="problem-title">The Problem &gt; <strong>The Solution</strong></h2>
  <div class="problem-copy">
    <p>K7 was started to solve significant problems associated with rapidly bringing innovative and transformational IP to market. &nbsp;These costly problems include:</p>
    <ul>
      <li><svg width="12" height="11" viewBox="0 0 12 11"><path d="M0 4h7V0l5 5.5L7 11V7H0z" fill="#fff"/></svg>Incomplete strategic planning, Difficulty finding leadership,</li>
      <li><svg width="12" height="11" viewBox="0 0 12 11"><path d="M0 4h7V0l5 5.5L7 11V7H0z" fill="#fff"/></svg>Not able to differentiate a product or service from others that are already available, andIgnoring the needs of customer.</li>
    </ul>
    <p>(Capital shortages, poor locations, and scaling too soon can also cause a start-up to have problems.)</p>
  </div>
  <a class="problem-btn">Learn More</a>
</section>

<section class="team">
  <h2 class="section-title" style="top:2148px">Our <strong>Team</strong></h2>
  <div class="member" style="left:111px;top:2209px">
    <div class="photo" role="img" aria-label="Portrait of a smiling team member with arms crossed"></div>
    <div class="plate"><h4>Dale Ortmann</h4></div>
    <p>30+ years of marketing, sales,<br>product development, and operations<br>executive leader in the life science</p>
    <div class="email"><svg width="14" height="11" viewBox="0 0 24 18"><path fill="var(--blue)" d="M0 0h24v3L12 10 0 3zM0 6l12 7 12-7v12H0z"/></svg>dale@k7mc.com</div>
  </div>
  <div class="member mid" style="left:464px;top:2241px">
    <div class="photo" role="img" aria-label="Portrait of a smiling team member"></div>
    <div class="plate"><h4>Nina Halvorsen</h4></div>
    <p>30+ years working in diagnostic and<br>medical device area with focus on<br>creative solutions</p>
    <div class="email"><svg width="14" height="11" viewBox="0 0 24 18"><path fill="var(--blue)" d="M0 0h24v3L12 10 0 3zM0 6l12 7 12-7v12H0z"/></svg>nina@k7mc.com</div>
  </div>
  <div class="member" style="left:815px;top:2209px">
    <div class="photo" role="img" aria-label="Portrait of a smiling team member in a grey shirt"></div>
    <div class="plate"><h4>Reed Calloway</h4></div>
    <p>30+ years accomplished CEO and<br>well-rounded executive with more<br>than 25 years of experience in</p>
    <div class="email"><svg width="14" height="11" viewBox="0 0 24 18"><path fill="var(--blue)" d="M0 0h24v3L12 10 0 3zM0 6l12 7 12-7v12H0z"/></svg>reed@k7mc.com</div>
  </div>
</section>

<section class="contact">
  <h2 class="section-title" style="top:2706px">Get In <strong>Touch With Us</strong></h2>
  <div class="contact-head">Address</div>
  <div class="info-row" style="top:2820px">
    <span class="info-icon"><svg width="16" height="20" viewBox="0 0 16 20"><path fill="#fff" d="M8 0a8 8 0 0 0-8 8c0 6 8 12 8 12s8-6 8-12a8 8 0 0 0-8-8zm0 11a3 3 0 1 1 0-6 3 3 0 0 1 0 6z"/></svg></span>
    <span>K7 Momentum Collective<br>United States</span>
  </div>
  <div class="info-row" style="top:2896px">
    <span class="info-icon"><svg width="18" height="18" viewBox="0 0 24 24"><path fill="#fff" d="M6.6 10.8a15 15 0 0 0 6.6 6.6l2.2-2.2a1 1 0 0 1 1-.25 11 11 0 0 0 3.6.6 1 1 0 0 1 1 1V20a1 1 0 0 1-1 1A17 17 0 0 1 3 4a1 1 0 0 1 1-1h3.5a1 1 0 0 1 1 1c0 1.25.2 2.45.6 3.6a1 1 0 0 1-.25 1z"/></svg></span>
    <span>+1 555 010 4477</span>
  </div>
  <div class="info-row" style="top:2971px">
    <span class="info-icon"><svg width="18" height="14" viewBox="0 0 24 18"><path fill="#fff" d="M0 0h24v3L12 10 0 3zM0 6l12 7 12-7v12H0z"/></svg></span>
    <span>info@k7momentumcollective.com</span>
  </div>
  <div class="field" style="left:509px;top:2773px;width:282px;height:49px">First Name</div>
  <div class="field" style="left:802px;top:2773px;width:284px;height:49px">Last Name</div>
  <div class="field" style="left:509px;top:2836px;width:282px;height:48px">Your Phone</div>
  <div class="field" style="left:802px;top:2836px;width:284px;height:48px">Your Email</div>
  <div class="field" style="left:509px;top:2900px;width:577px;height:110px">Message</div>
  <a class="btn submit">SUBMIT</a>
</section>

<footer class="footer">
  <svg class="abs" style="left:0;top:0" width="1200" height="475" viewBox="0 0 1200 475">
    <path d="M0 140 Q 600 40 1200 110 L1200 475 L0 475 Z" fill="var(--black)"/>
  </svg>
  <div class="footer-brand">THE K7 MOMENTUM COLLECTIVE</div>
  <a class="footer-nav" style="left:226px">Home</a>
  <a class="footer-nav" style="left:315px">About</a>
  <a class="footer-nav" style="left:416px">Our Team</a>
  <a class="footer-nav" style="left:545px">Plan Elements</a>
  <a class="footer-nav" style="left:686px">The Solutions</a>
  <a class="footer-nav" style="left:824px">Our Partners</a>
  <a class="footer-nav" style="left:954px">Contact Us</a>
  <span class="fsocial" style="left:505px"></span>
  <span class="fsocial" style="left:557px"></span>
  <span class="fsocial" style="left:609px"></span>
  <span class="fsocial" style="left:661px"></span>
  <div class="copyright">Copyrights@2023.K7 Momentum Collective.All Rights Reserved</div>
</footer>

</body>
</html>
```